Banner to be displayed at local Farmers Market Booth.

Graphic Design Brief: Farmers Market Banner Contest

Project Overview:We are seeking talented graphic designers to create a visually appealing banner for our booth at the local farmers market. Our company specializes in healthy, all-natural dog and cat treats, and we want a banner that captures our brand identity while drawing in pet owners who value quality and nutrition for their furry friends.

Banner Specifications:

Size: 24 inches x 60 inches (Horizontal orientation) 24" High X 60 wide

Theme: Vintage/Retro

Style: Warm, inviting, nostalgic with a touch of rustic charm

Colors: Earthy, muted tones such as warm browns, soft greens, and creamy yellows. Pops of red or blue may be used sparingly for accents. OR Black and White with gray scales. Would like to see both

Typography: Retro-style fonts that are readable and align with the vintage aesthetic.

Key Elements to Include: website (www.moltbyfarms.com)

Company Name: Moltby Farms

Tagline: " Simply Honest Bites "
Imagery: Illustrations or stylized graphics of happy dogs and cats, possibly interacting with treats.

Emphasis on Natural Ingredients: Icons or design elements that subtly suggest freshness and quality (e.g., leaves, wheat, bones, or paw prints).

Farmers Market Appeal: A design that blends well with the artisanal, handmade, and farm-fresh atmosphere of the market.

Design Considerations:

The banner should be easily readable from a distance.

A balanced composition that doesn't feel overcrowded.

Should evoke trust and warmth while maintaining a professional look.

Avoid overly modern or sleek elements that don’t align with the vintage aesthetic.

Submission Requirements:

High-resolution digital file in PDF or AI format.

CMYK color mode for printing purposes.

Must include a mockup or preview of how it would look in a real farmers market setting.

We look forward to seeing your creative interpretations of our brand! If you have any questions, feel free to reach out.

Font styles to use
Other font styles liked:
• See attachement

Requirements
Nice to have
• Retro/Vintage,playful BUT NOT whimsical

```html
<!DOCTYPE html>
<html lang="en">
<head>
<meta charset="utf-8">
<title>Moltby Farms – Market Banner</title>
<link rel="stylesheet" href="https://fonts.googleapis.com/css2?family=Lobster&family=Amatic+SC:wght@700&family=Caveat+Brush&display=swap">
<style>
  :root {
    --page: #f4f1ea;
    --green-deep: #2f9a45;
    --green-mid: #6cc25a;
    --green-light: #b9dc6a;
    --brand-red: #a83a2c;
    --ribbon-fold: #8e2f23;
    --cream: #fbefb8;
    --teal-stitch: #2c5a6b;
    --ink: #1a1a1a;
    --white: #ffffff;
    --art-light: #fde9b6;
    --art-warm: #f7c97a;
    --art-brown: #b98a3e;
  }
  html, body {
    margin: 0;
    padding: 0;
    width: 1200px;
    height: 1161px;
    overflow: hidden;
    background: var(--page);
  }
  .banner {
    position: absolute;
    left: 0;
    top: 342px;
    width: 1200px;
    height: 477px;
    display: block;
  }
  .brand-title {
    font-family: "Lobster", cursive;
    font-size: 148px;
    fill: var(--white);
    filter: drop-shadow(6px 6px 0 var(--ink));
  }
  .tagline {
    font-family: "Amatic SC", sans-serif;
    font-weight: 700;
    font-size: 44px;
    fill: var(--cream);
  }
  .web-address {
    font-family: "Caveat Brush", cursive;
    font-size: 36px;
    fill: var(--cream);
  }
  .badge-name {
    font-family: "Caveat Brush", cursive;
    font-size: 34px;
    fill: var(--cream);
  }
</style>
</head>
<body>
<svg class="banner" viewBox="0 0 1200 477" xmlns="http://www.w3.org/2000/svg">
  <defs>
    <radialGradient id="burst-field" cx="0.4" cy="0.62" r="0.75">
      <stop offset="0" stop-color="var(--green-light)"/>
      <stop offset="0.45" stop-color="var(--green-mid)"/>
      <stop offset="1" stop-color="var(--green-deep)"/>
    </radialGradient>
    <radialGradient id="art-glow" cx="0.45" cy="0.3" r="0.8">
      <stop offset="0" stop-color="var(--art-light)"/>
      <stop offset="0.5" stop-color="var(--art-warm)"/>
      <stop offset="1" stop-color="var(--art-brown)"/>
    </radialGradient>
  </defs>

  <rect class="background" x="0" y="0" width="1200" height="477" fill="url(#burst-field)"/>

  <rect class="illustration" x="865" y="20" width="323" height="440" rx="150" ry="150"
        fill="url(#art-glow)" role="img"
        aria-label="Illustration area in warm golden tones"/>

  <text class="brand-title" x="40" y="230" textLength="805" lengthAdjust="spacingAndGlyphs"
        transform="rotate(-7 40 230)">Moltby Farms</text>

  <g class="ribbon" transform="translate(430 300) rotate(-12)">
    <polygon points="-205,-40 -135,-40 -135,10 -205,10 -185,-15" fill="var(--ribbon-fold)"/>
    <polygon points="205,-70 135,-70 135,-20 205,-20 185,-45" fill="var(--ribbon-fold)"/>
    <rect x="-160" y="-30" width="320" height="64" fill="var(--brand-red)"/>
    <rect x="-152" y="-23" width="304" height="50" fill="none" stroke="var(--cream)"
          stroke-width="1.5" stroke-dasharray="4 4"/>
    <text class="tagline" x="0" y="14" text-anchor="middle">Simply Honest Bites</text>
  </g>

  <rect class="web-band" x="0" y="370" width="650" height="50" fill="var(--brand-red)"/>
  <text class="web-address" x="104" y="406" textLength="395" lengthAdjust="spacingAndGlyphs">www.moltbyfarms.com</text>

  <rect class="bottom-line" x="0" y="449" width="1200" height="4" fill="var(--brand-red)"/>
  <rect class="bottom-strip" x="0" y="453" width="1200" height="24" fill="var(--cream)"/>

  <g class="badge">
    <circle cx="725" cy="358" r="107" fill="var(--brand-red)"/>
    <circle cx="725" cy="358" r="92" fill="var(--cream)"/>
    <circle cx="725" cy="358" r="85" fill="none" stroke="var(--teal-stitch)" stroke-width="1.5" stroke-dasharray="6 5"/>
    <circle cx="725" cy="358" r="72" fill="var(--brand-red)"/>
    <text class="badge-name" x="725" y="370" text-anchor="middle">Moltby</text>
  </g>
</svg>
</body>
</html>
```